Flyer Design Project

I require a double sided flyer in PSD format.
The flyer should look fresh and clean.
The flyer is for an digital marketing company that offers various services. The services are broken down into 3 main categories and the design should reflect this.
All the content is provided in the attached file
Industry/Entity Type
Digital
Requirements
Must have
- Front of the leaflet to be mainly white background with appealing text based questions in the colours in large font with relevant images.
Back if the
3 separate boxes using the colours indicated in the attachment for the services on back of the leafet.
Should not have
- Gradients
Borders on the edges of the design
Vignettes
Black elements
Any text below 10pt
Fancy fonts
Do not use old-style fonts

```html
<!DOCTYPE html>
<html lang="en">
<head>
<meta charset="utf-8">
<title>Kavora – Grow Your Business Online</title>
<link rel="stylesheet" href="https://fonts.googleapis.com/css2?family=Oswald:wght@600;700&family=Open+Sans:wght@400&display=swap">
<style>
  :root {
    --cyan: #3fb8dc;
    --slate: #444d5e;
    --ink: #3d4556;
    --green: #a9cc35;
    --orange: #f38a10;
    --white: #ffffff;
    --mist: #e9ecef;
  }
  * { margin: 0; padding: 0; box-sizing: border-box; }
  html, body { width: 845px; height: 1200px; overflow: hidden; background: var(--cyan); }
  .flyer {
    position: relative;
    width: 845px;
    height: 1200px;
    background: var(--cyan);
    font-family: "Open Sans", Arial, sans-serif;
    overflow: hidden;
  }
  .body-panel {
    position: absolute;
    left: 0; top: 150px;
    width: 845px; height: 910px;
    background: linear-gradient(to bottom, var(--white) 0%, var(--white) 85%, var(--mist) 100%);
  }
  .header {
    position: absolute;
    left: 12px; top: 22px;
    width: 833px; height: 136px;
    background: var(--slate);
    border-radius: 30px 0 0 30px;
  }
  .header::before, .footer::before, .question::before {
    content: "";
    position: absolute;
    left: 5px; top: 5px; right: 0; bottom: 5px;
    border: 2px solid rgba(255,255,255,0.9);
    border-right: none; border-bottom: none;
    border-radius: 24px 0 0 0;
    pointer-events: none;
  }
  .brand {
    position: absolute;
    left: 36px; top: 28px;
    font-size: 60px;
    font-weight: 400;
    color: var(--cyan);
    letter-spacing: 1px;
    line-height: 1;
  }
  .call {
    position: absolute;
    left: 421px; top: 30px;
    font-size: 33px;
    line-height: 44px;
    color: var(--white);
  }
  .call .phone { color: var(--cyan); }
  .illustration {
    position: absolute;
    left: 0; top: 180px;
    width: 330px; height: 815px;
    background: linear-gradient(160deg, #2f7fcf 0%, #1f5ea8 45%, #d9dde2 100%);
    border-radius: 0 160px 20px 0;
  }
  .question {
    position: absolute;
    left: 283px;
    width: 562px;
    border-radius: 28px 0 0 28px;
    padding-left: 52px;
  }
  .question h2 {
    font-family: "Oswald", "Arial Narrow", sans-serif;
    font-weight: 700;
    font-size: 47px;
    line-height: 52px;
    color: var(--ink);
    letter-spacing: -0.3px;
  }
  .q-stat { top: 206px; height: 227px; background: var(--green); padding-top: 22px; }
  .q-found { top: 484px; height: 177px; background: var(--cyan); padding-top: 30px; }
  .q-more { top: 719px; height: 207px; background: var(--orange); padding-top: 26px; }
  .tagline {
    position: absolute;
    left: 288px; top: 988px;
    font-size: 26px;
    color: #1e1e24;
  }
  .footer {
    position: absolute;
    left: 12px; top: 1047px;
    width: 833px; height: 123px;
    background: var(--slate);
    border-radius: 30px 0 0 30px;
  }
  .web {
    position: absolute;
    left: 46px; top: 44px;
    font-size: 27px;
    color: var(--white);
  }
  .web span { color: var(--cyan); }
  .address {
    position: absolute;
    left: 434px; top: 42px;
    font-size: 17.5px;
    line-height: 25px;
    color: var(--white);
  }
</style>
</head>
<body>
  <main class="flyer">
    <div class="body-panel"></div>

    <header class="header">
      <div class="brand">KAVORA</div>
      <p class="call">Call <span class="phone">0121 555 0148</span> for<br>a FREE consultation</p>
    </header>

    <div class="illustration" role="img" aria-label="Illustration of a thoughtful figure sitting on a large blue question mark"></div>

    <section class="question q-stat">
      <h2>Did You Know 85% of<br>Consumers Use<br>The Internet To Find<br>Businesses Like Yours?</h2>
    </section>
    <section class="question q-found">
      <h2>Are Your Customers<br>Finding You Online?</h2>
    </section>
    <section class="question q-more">
      <h2>Do You Need More<br>Customers For<br>Your Business?</h2>
    </section>

    <p class="tagline">Let us help you grow your business online</p>

    <footer class="footer">
      <p class="web">www.<span>kavora</span>.co.uk</p>
      <p class="address">24 Orchard House | 118 Linden Road<br>Birmingham | B15 3QT | 0121 555 0148</p>
    </footer>
  </main>
</body>
</html>
```